Create modern and sleek business card for luxury real estate company

We're a "boutique" real estate office looking for a design that gets across a highly modern luxury brand. Blacks and whites are probably the best colors unless we try a silver foil for the logo. I've attached a version of our current logo here. I'd like to swap out the current font on there with Gotham Light Regular.

I'm looking to have one side of the card have the logo with the space for our agents info on the other side.

Target Market(s)

Young professionals in a "luxury" headspace

Industry/Entity Type

Real estate

Contact Information for Business Card

A place for agent name, cell number, website. The slogan "Simply Rethinking Real Estate".

Font styles to use
Other font styles liked:
• Gotham Regular

Colors

Designer to choose only greyscale colors for use in the design.

Requirements
Must have
• Matte black as the background color. Clean lines and use of contrast. A specific design aspect that will use silver foil.
Nice to have
• Up in the air on integrating a QR code
Should not have
• Any houses or other real estate related design (ex: a clip art house)

```html
<!DOCTYPE html>
<html lang="en">
<head>
<meta charset="utf-8">
<title>Larkmont Realty Business Card</title>
<link href="https://fonts.googleapis.com/css2?family=Open+Sans:ital,wght@0,400;0,600;0,700;1,400&display=swap" rel="stylesheet">
<style>
  :root {
    --stage: #1c1c1c;
    --card: #121212;
    --card-edge: #262626;
    --ink: #f2f2f2;
    --silver: #c9c9c9;
    --muted: #7a7a7a;
    --rule: #5c5c5c;
  }
  * { margin: 0; padding: 0; box-sizing: border-box; }
  html, body { width: 1200px; height: 900px; overflow: hidden; }
  body {
    background: var(--stage);
    font-family: "Open Sans", sans-serif;
    color: var(--ink);
    position: relative;
  }
  .card {
    position: absolute;
    left: 285px;
    width: 630px;
    height: 360px;
    background: var(--card);
    border: 1px solid var(--card-edge);
    box-shadow: 0 18px 40px rgba(0,0,0,0.55);
  }
  .card--front { top: 75px; }
  .card--back { top: 465px; }

  .brand {
    position: absolute;
    display: flex;
    align-items: center;
    gap: 18px;
  }
  .card--front .brand { left: 150px; top: 62px; }
  .card--back .brand { left: 50%; top: 50%; transform: translate(-50%, -50%); }
  .brand__circle {
    width: 64px; height: 64px;
    border: 2px solid var(--silver);
    border-radius: 50%;
    flex: none;
  }
  .brand__name {
    font-weight: 400;
    font-size: 30px;
    letter-spacing: 4px;
    line-height: 1.15;
    color: var(--silver);
    text-transform: uppercase;
  }
  .card--back .brand__circle { border-color: #3a3a3a; }
  .card--back .brand__name { color: #8e8e8e; }

  .agent {
    position: absolute;
    left: 60px;
    top: 220px;
    width: 200px;
    text-align: right;
  }
  .agent__name {
    font-weight: 700;
    font-size: 19px;
    letter-spacing: 1px;
    text-transform: uppercase;
  }
  .agent__title {
    font-style: italic;
    font-size: 15px;
    color: var(--muted);
    margin-top: 2px;
  }
  .divider {
    position: absolute;
    left: 285px;
    top: 214px;
    width: 1px;
    height: 82px;
    background: var(--rule);
  }
  .contact {
    position: absolute;
    left: 308px;
    top: 214px;
    list-style: none;
  }
  .contact__item {
    display: flex;
    align-items: center;
    gap: 10px;
    font-size: 16px;
    line-height: 27px;
  }
  .contact__icon { width: 13px; height: 13px; fill: var(--muted); flex: none; }
</style>
</head>
<body>
  <section class="card card--front" aria-label="Business card, info side">
    <div class="brand">
      <span class="brand__circle"></span>
      <span class="brand__name">Larkmont<br>Realty</span>
    </div>
    <div class="agent">
      <p class="agent__name">Dorian Vale</p>
      <p class="agent__title">President</p>
    </div>
    <span class="divider"></span>
    <ul class="contact">
      <li class="contact__item">
        <svg class="contact__icon" viewBox="0 0 16 16"><path d="M3.6 1.2l2.4 2.6-1.4 2a10 10 0 0 0 5.6 5.6l2-1.4 2.6 2.4-1.6 2.2C7.4 14.4 1.6 8.6 1.4 2.8z"/></svg>
        555-014-2278
      </li>
      <li class="contact__item">
        <svg class="contact__icon" viewBox="0 0 16 16"><path d="M1 3h14v1.2L8 9 1 4.2z"/><path d="M1 5.8l7 4.8 7-4.8V13H1z"/></svg>
        hello@larkmontrealty.com
      </li>
      <li class="contact__item">
        <svg class="contact__icon" viewBox="0 0 16 16"><circle cx="8" cy="8" r="7"/></svg>
        www.larkmontrealty.com
      </li>
    </ul>
  </section>

  <section class="card card--back" aria-label="Business card, logo side">
    <div class="brand">
      <span class="brand__circle"></span>
      <span class="brand__name">Larkmont<br>Realty</span>
    </div>
  </section>
</body>
</html>
```